Marlowe Crest Realty business card design

Looking for an upscale and clean business card design and updated logo. I sell to a very high-end south Florida real estate market.
Target Market(s)
High-end real estate in south Florida real estate market
Industry/Entity Type
Real Estate Agent
Contact Information for Business Card
Marlowe Crest Realty, Inc
738 West Pinecrest Ave, Suite 410/510, Fort Lauderdale, FL 33308
Gary Whitlock - Broker/Owner
954-327-8846 Direct
garyshomes@quellmail.com
Website: DwellTarrowBay.com
Font styles to use
Other font styles liked:
- Copperplate Gothic, Georgia, etc.
Requirements
Must have
- My photo, company name, my name and title, all info stated in Details above
Nice to have
- Luxury home design element, waterfront

```html
<!DOCTYPE html>
<html lang="en">
<head>
<meta charset="utf-8">
<title>Marlowe Crest Realty – Business Card</title>
<link rel="stylesheet" href="https://fonts.googleapis.com/css2?family=Cinzel:wght@700&family=Cormorant+Garamond:wght@500&family=Montserrat:wght@400;500&display=swap">
<style>
  :root {
    --backdrop: #333333;
    --card-black: #141414;
    --card-black-soft: #1d1d1d;
    --paper-white: #f4f4f2;
    --gold: #f0c419;
    --gold-deep: #d9a816;
    --text-white: #f2f2f2;
    --photo-light: #d9d4cc;
    --photo-blue: #2c4a8a;
  }
  * { box-sizing: border-box; margin: 0; padding: 0; }
  html, body {
    width: 1200px; height: 800px; overflow: hidden;
    background: var(--backdrop);
  }
  .canvas {
    position: relative; width: 1200px; height: 800px;
  }
  .card {
    position: absolute; left: 280px; width: 640px; height: 366px;
    background: var(--card-black);
    border-bottom: 4px solid var(--gold);
    overflow: hidden;
  }
  .card--front { top: 24px; }
  .card--back { top: 410px; }

  /* front */
  .paper-strip {
    position: absolute; left: 0; top: 0; bottom: 0; width: 118px;
    background: var(--paper-white);
    border-right: 5px solid var(--gold);
  }
  .sunburst-decor {
    position: absolute; left: 330px; top: 40px; width: 360px; height: 330px;
    background: radial-gradient(circle at 45% 50%, #1a1a1a 0 26%, #202020 27% 30%, #171717 31% 60%, var(--card-black) 75%);
  }
  .portrait {
    position: absolute; left: 44px; top: 60px; width: 156px; height: 156px;
    border-radius: 50%;
    border: 4px solid var(--gold);
    background: linear-gradient(180deg, var(--photo-light) 0 52%, var(--photo-blue) 53% 100%);
  }
  .brand {
    position: absolute; left: 260px; top: 44px;
    display: flex; align-items: center; gap: 10px;
  }
  .brand__dot {
    width: 14px; height: 14px; border-radius: 50%; background: var(--gold);
  }
  .brand__name {
    font-family: "Cormorant Garamond", Georgia, serif; font-weight: 500;
    font-size: 19px; line-height: 1.1; color: var(--text-white);
  }
  .details {
    position: absolute; left: 232px; top: 120px;
    font-family: "Montserrat", Arial, sans-serif; color: var(--text-white);
  }
  .details__name {
    font-family: "Cinzel", Georgia, serif; font-weight: 700;
    font-size: 30px; letter-spacing: 2px; color: var(--gold); line-height: 1.1;
  }
  .details__title { font-size: 15px; margin-top: 2px; }
  .details__company { font-size: 15px; color: var(--gold); margin-top: 10px; }
  .details__address { font-size: 14px; line-height: 1.35; margin-top: 2px; }
  .contact { list-style: none; margin-top: 12px; font-size: 14px; line-height: 1.5; }
  .contact li { display: flex; align-items: center; gap: 9px; }
  .contact svg { width: 13px; height: 13px; fill: var(--gold); flex: none; }
  .contact .accent { color: var(--gold); }

  /* back */
  .pattern-field {
    position: absolute; inset: 0;
    background: linear-gradient(120deg, #2a2a2a 0%, #1a1a1a 40%, var(--card-black) 100%);
  }
  .back-brand {
    position: absolute; right: 70px; bottom: 48px;
    display: flex; align-items: center; gap: 10px;
  }
</style>
</head>
<body>
<main class="canvas">
  <section class="card card--front" aria-label="Business card front">
    <div class="paper-strip"></div>
    <div class="sunburst-decor" role="img" aria-label="Large faint embossed sunburst decoration"></div>
    <div class="portrait" role="img" aria-label="Portrait photo of Gary Whitlock"></div>
    <div class="brand">
      <span class="brand__dot"></span>
      <span class="brand__name">Marlowe Crest<br>Realty, Inc.</span>
    </div>
    <div class="details">
      <h1 class="details__name">Gary Whitlock</h1>
      <p class="details__title">Broker/Owner</p>
      <p class="details__company">Marlowe Crest Realty, Inc</p>
      <p class="details__address">738 West Pinecrest Ave,<br>Suite 410/510,<br>Fort Lauderdale, FL 33308</p>
      <ul class="contact">
        <li><svg viewBox="0 0 24 24"><path d="M6.6 10.8a15.1 15.1 0 006.6 6.6l2.2-2.2a1 1 0 011-.25 11.4 11.4 0 003.6.6 1 1 0 011 1V20a1 1 0 01-1 1A17 17 0 013 4a1 1 0 011-1h3.5a1 1 0 011 1 11.4 11.4 0 00.6 3.6 1 1 0 01-.25 1z"/></svg>954-327-8846</li>
        <li><svg viewBox="0 0 24 24"><path d="M2 5h20v14H2z M2 5l10 8 10-8" fill="none" stroke="#f0c419" stroke-width="2"/></svg>garyshomes@quellmail.com</li>
        <li><svg viewBox="0 0 24 24"><circle cx="12" cy="12" r="10"/></svg>www.<span class="accent">DwellTarrowBay</span>.com</li>
      </ul>
    </div>
  </section>

  <section class="card card--back" aria-label="Business card back">
    <div class="pattern-field" role="img" aria-label="Repeating embossed sunburst pattern"></div>
    <div class="back-brand">
      <span class="brand__dot"></span>
      <span class="brand__name">Marlowe Crest Realty</span>
    </div>
  </section>
</main>
</body>
</html>
```